Company identity deisgn should support 2 languages

I would like to get our company identity design
This includes the following only
Business Cards 2 languages Arabic and English
Email signature
Letterhead
Linkedin profile images
Attached is the logo in Ai format

Requirements
Must have
• For business card
Must have
Name and Adrees in arabic
Name and Address in english
You might use both side of the card
Should not have
• Any pictures other than the logo

```html
<!DOCTYPE html>
<html lang="en">
<head>
<meta charset="utf-8">
<title>Nova Cortex Systems – Business Cards</title>
<link rel="stylesheet" href="https://fonts.googleapis.com/css2?family=Poppins:wght@400;500;600&family=Noto+Sans+Arabic:wght@400;600&display=swap">
<style>
  :root {
    --page-bg: #8a8a8a;
    --card-bg: #ffffff;
    --brand-blue: #0e76bf;
    --swoosh-grey: #b3b4b8;
    --text-dark: #3c3c3c;
  }
  html, body {
    margin: 0;
    padding: 0;
    width: 1200px;
    height: 1200px;
    overflow: hidden;
    background: var(--page-bg);
    font-family: "Poppins", sans-serif;
  }
  .card {
    position: absolute;
    left: 200px;
    width: 800px;
    height: 457px;
    background: var(--card-bg);
    border-radius: 30px;
    overflow: hidden;
  }
  .card--english { top: 120px; }
  .card--arabic { top: 630px; }
  .card__wave {
    position: absolute;
    inset: 0;
    width: 800px;
    height: 457px;
  }
  .card__person {
    position: absolute;
    right: 43px;
    top: 40px;
    text-align: right;
    color: #fff;
  }
  .person__name {
    font-size: 26px;
    font-weight: 500;
    letter-spacing: 0.3px;
    line-height: 1.2;
  }
  .person__title {
    font-size: 18px;
    line-height: 1.2;
  }
  .card--arabic .card__person { font-family: "Noto Sans Arabic", sans-serif; direction: rtl; top: 42px; }
  .card--arabic .person__name { font-size: 26px; font-weight: 600; }
  .card--arabic .person__title { font-size: 19px; font-weight: 600; }
  .brand {
    position: absolute;
    left: 46px;
    top: 208px;
    display: flex;
    align-items: center;
    gap: 12px;
  }
  .brand__dot {
    width: 40px;
    height: 40px;
    border-radius: 50%;
    background: var(--brand-blue);
  }
  .brand__name {
    font-size: 24px;
    font-weight: 500;
    color: var(--brand-blue);
    letter-spacing: 0.5px;
  }
  .contacts {
    position: absolute;
    left: 46px;
    top: 318px;
    margin: 0;
    padding: 0;
    list-style: none;
    color: var(--text-dark);
    font-size: 18px;
    line-height: 23px;
  }
  .contacts li {
    display: flex;
    align-items: center;
    gap: 9px;
  }
  .contacts svg { width: 15px; height: 15px; fill: var(--brand-blue); }
  .address {
    position: absolute;
    right: 43px;
    bottom: 42px;
    text-align: right;
    color: var(--text-dark);
    font-size: 18px;
    line-height: 23px;
    font-style: normal;
  }
  .address .site { display: block; margin-top: 3px; }
  .address__ar { font-family: "Noto Sans Arabic", sans-serif; direction: rtl; font-size: 16px; line-height: 26px; }
</style>
</head>
<body>

<svg width="0" height="0" style="position:absolute">
  <defs>
    <path id="wave-shape" d="M0,158 C30,120 70,78 130,50 C220,10 300,60 430,110 C560,160 700,180 800,145 V0 H0 Z"/>
    <symbol id="icon-phone" viewBox="0 0 16 16"><path d="M3.5 1l2.5 3-1.5 1.8c.8 1.9 2.3 3.4 4.2 4.2L10.5 8.5l3 2.5-1.2 2.8C7 14 2 9 2.2 2.2z"/></symbol>
    <symbol id="icon-mobile" viewBox="0 0 16 16"><path d="M4 1h8v14H4zM5.5 2.5v9h5v-9z"/></symbol>
    <symbol id="icon-fax" viewBox="0 0 16 16"><path d="M4 1h6l2 2v3H4zM1 7h14v5H1zM3 13h10v2H3z"/></symbol>
    <symbol id="icon-mail" viewBox="0 0 16 16"><path d="M1 4h14v9H1zM2.5 5.5L8 9.5l5.5-4z"/></symbol>
  </defs>
</svg>

<section class="card card--english" lang="en">
  <svg class="card__wave" viewBox="0 0 800 457" aria-hidden="true">
    <use href="#wave-shape" fill="var(--swoosh-grey)" transform="translate(0,13)"/>
    <use href="#wave-shape" fill="#ffffff" transform="translate(0,5)"/>
    <use href="#wave-shape" fill="var(--brand-blue)"/>
  </svg>
  <div class="card__person">
    <div class="person__name">DANIEL HAYES</div>
    <div class="person__title">President</div>
  </div>
  <div class="brand"><span class="brand__dot"></span><span class="brand__name">NOVA CORTEX SYSTEMS</span></div>
  <ul class="contacts">
    <li><svg><use href="#icon-phone"/></svg>555-014-2731</li>
    <li><svg><use href="#icon-mobile"/></svg>555-019-4862</li>
    <li><svg><use href="#icon-fax"/></svg>555-017-3390</li>
    <li><svg><use href="#icon-mail"/></svg>hello@novacortexlabs.com</li>
  </ul>
  <address class="address">
    214 Cedar Hollow Road<br>
    Fairbanks, Alaska 99701
    <span class="site">novacortexlabs.com</span>
  </address>
</section>

<section class="card card--arabic">
  <svg class="card__wave" viewBox="0 0 800 457" aria-hidden="true">
    <use href="#wave-shape" fill="var(--swoosh-grey)" transform="translate(0,13)"/>
    <use href="#wave-shape" fill="#ffffff" transform="translate(0,5)"/>
    <use href="#wave-shape" fill="var(--brand-blue)"/>
  </svg>
  <div class="card__person" lang="ar">
    <div class="person__name">دانيال هايز</div>
    <div class="person__title">رئيس</div>
  </div>
  <div class="brand"><span class="brand__dot"></span><span class="brand__name">NOVA CORTEX SYSTEMS</span></div>
  <ul class="contacts">
    <li><svg><use href="#icon-phone"/></svg>555-014-2731</li>
    <li><svg><use href="#icon-mobile"/></svg>555-019-4862</li>
    <li><svg><use href="#icon-fax"/></svg>555-017-3390</li>
    <li><svg><use href="#icon-mail"/></svg>hello@novacortexlabs.com</li>
  </ul>
  <address class="address">
    <span class="address__ar" lang="ar">214 طريق سيدار هولو<br>فيربانكس ، ألاسكا 99701</span>
    <span class="site">novacortexlabs.com</span>
  </address>
</section>

</body>
</html>
```